Business Card For Halvenmoor Financial Consulting

Hi, I would like a business card designed. Bold, modern.
Please use the same design as the logo. I have also attached the website design to see the overall theme.
Wordmark Font
Color: Hex: #01AEF7

```html
<!DOCTYPE html>
<html lang="en">
<head>
<meta charset="UTF-8">
<title>Halvenmoor Financial Consulting – Business Card</title>
<link rel="stylesheet" href="https://fonts.googleapis.com/css2?family=Montserrat:wght@400;500;700;800&display=swap">
<style>
  :root {
    --page-bg: #8d8d8d;
    --card-bg: #16222c;
    --brand-blue: #01aef7;
    --text-light: #ffffff;
  }
  * { box-sizing: border-box; margin: 0; padding: 0; }
  html, body {
    width: 1160px; height: 1200px; overflow: hidden;
    background: var(--page-bg);
    font-family: "Montserrat", Arial, sans-serif;
  }
  .canvas { position: relative; width: 1160px; height: 1200px; }
  .card {
    position: absolute; left: 199px; width: 777px; height: 442px;
    background: var(--card-bg); color: var(--text-light);
  }
  .card--front { top: 105px; }
  .card--back { top: 634px; }

  .brand { display: flex; align-items: center; gap: 12px; position: absolute; }
  .brand__mark { background: var(--brand-blue); flex: none; }
  .brand__name {
    font-weight: 700; color: var(--text-light); text-transform: uppercase; line-height: 1.05;
  }
  .brand__name span { display: block; }
  .brand__name .brand__sub { letter-spacing: 0.32em; }

  .card--front .brand { left: 44px; top: 52px; }
  .card--front .brand__mark { width: 44px; height: 44px; }
  .card--front .brand__name { font-size: 27px; letter-spacing: 0.04em; }
  .card--front .brand__sub { font-size: 9.5px; margin-top: 5px; }

  .card--back .brand { left: 50%; top: 50%; transform: translate(-50%, -50%); gap: 18px; }
  .card--back .brand__mark { width: 80px; height: 80px; }
  .card--back .brand__name { font-size: 48px; letter-spacing: 0.04em; }
  .card--back .brand__sub { font-size: 16.5px; margin-top: 10px; }

  .person { position: absolute; right: 32px; top: 46px; text-align: right; }
  .person__name {
    font-size: 30px; font-weight: 800; color: var(--brand-blue);
    text-transform: uppercase; letter-spacing: 0.01em; line-height: 1.1;
  }
  .person__role { font-size: 19px; font-weight: 400; margin-top: 4px; }

  .contact-list { position: absolute; left: 31px; top: 313px; list-style: none; }
  .contact-list li {
    display: flex; align-items: center; gap: 9px; height: 37px;
    font-size: 19px; font-weight: 400;
  }
  .contact-list svg { width: 24px; height: 24px; flex: none; }

  .address {
    position: absolute; right: 34px; top: 357px; text-align: right;
    font-size: 19px; line-height: 28px; font-style: normal;
  }
</style>
</head>
<body>
<main class="canvas">
  <section class="card card--front" aria-label="Card front">
    <div class="brand">
      <div class="brand__mark"></div>
      <p class="brand__name"><span>Halvenmoor</span><span class="brand__sub">Financial Consulting</span></p>
    </div>

    <div class="person">
      <p class="person__name">Orin Castell</p>
      <p class="person__role">Senior Consultant</p>
    </div>

    <ul class="contact-list">
      <li>
        <svg viewBox="0 0 24 24" aria-hidden="true"><circle cx="12" cy="12" r="12" fill="#01aef7"/><path d="M6 10c0-2 3-3 6-3s6 1 6 3l-1 1.5-2.5-.5V9.5h-5V11L7 11.5Z M8 12h8l1 5H7Z" fill="#fff"/></svg>
        <span>+1 555 204 7318</span>
      </li>
      <li>
        <svg viewBox="0 0 24 24" aria-hidden="true"><circle cx="12" cy="12" r="12" fill="#01aef7"/><rect x="6" y="8" width="12" height="8.5" rx="1" fill="#fff"/><path d="M6.5 8.5 12 13l5.5-4.5" fill="none" stroke="#01aef7" stroke-width="1.3"/></svg>
        <span>info@halvenmoor.com</span>
      </li>
      <li>
        <svg viewBox="0 0 24 24" aria-hidden="true"><circle cx="12" cy="12" r="12" fill="#01aef7"/><circle cx="12" cy="12" r="6.5" fill="none" stroke="#fff" stroke-width="1.4"/><ellipse cx="12" cy="12" rx="2.8" ry="6.5" fill="none" stroke="#fff" stroke-width="1.2"/><path d="M5.5 12h13" stroke="#fff" stroke-width="1.2"/></svg>
        <span>www.halvenmoor.com</span>
      </li>
    </ul>

    <address class="address">42 Larkspur Lane 9<br>Brookhaven, NY 11719</address>
  </section>

  <section class="card card--back" aria-label="Card back">
    <div class="brand">
      <div class="brand__mark"></div>
      <p class="brand__name"><span>Halvenmoor</span><span class="brand__sub">Financial Consulting</span></p>
    </div>
  </section>
</main>
</body>
</html>
```